gift box for organic and natural food items

My brand name is Tiller's Pantry and we are selling organic dried food to Korea now. We focus on transparent from the family farm to the customer directly with the single or simple organic ingredient. Our main customers are mainly woman from 30 to 50 years old. We have 4 different products for this package. Organic dried cherry, Organic dried figs, Organic dried dates and Organic dried pistachio. I would like to make a gift box that woman want to have and hold our natural products. The material of the gift box will be Royal Ivory Paper.

Target Market(s)

We will sell these items and gift box at the luxury department store.

Industry/Entity Type

Food Production

Font styles to use
Serif
Script

Colors
9ccb3b

Requirements
Must have
• Our slogan: A gift from the farm brought fresh to your door
• Our producer image: I will upload our producer's image
• We focus on the transparent and our producers.
• I will provide you with the image file for the only producers later.
Nice to have
• Brand logo / Our brand introduction sentences / NFCB logo / Color
• Color : Green & Bright Beige
• "Indulge. Nourish. Enjoy"
• "Taste the difference.
• The difference is quality.
• Quality you can experience"
• "As you savor the farm fresh delicacies enclosed in every box, relish in the fact that each ingredient was meticulously selected and directly sourced from hard working family farms. The result is a snacking experience like none other. With quality you can taste, our organic treats boast a unique flavor that will tantalize the taste buds. "
• "Upgrade your nourishment.
• Upgrade your nutrition.
• Upgrade your snack."
Should not have
• Too complicated with many colors

```html
<!DOCTYPE html>
<html lang="en">
<head>
<meta charset="utf-8">
<title>Tiller's Pantry — Organic Pistachio</title>
<link rel="stylesheet" href="https://fonts.googleapis.com/css2?family=Dancing+Script:wght@500&family=Josefin+Sans:wght@300&display=swap">
<style>
  :root {
    --leaf-green: #92c83e;
    --leaf-green-light: #a5d156;
    --deep-green: #3f8f4a;
    --cream-text: #eef3dc;
    --rule-brown: #6b5a3a;
    --seal-fill: #e6efcb;
    --nut-tan: #d9cfae;
    --nut-green: #7f9a3c;
  }
  html, body {
    margin: 0;
    padding: 0;
    width: 1200px;
    height: 1200px;
    overflow: hidden;
  }
  .package-front {
    position: relative;
    width: 1200px;
    height: 1200px;
    background: linear-gradient(160deg, var(--leaf-green-light) 0%, var(--leaf-green) 70%);
    overflow: hidden;
    font-family: 'Josefin Sans', sans-serif;
    color: var(--cream-text);
  }
  .brand-name {
    position: absolute;
    top: 140px;
    left: 0;
    width: 100%;
    text-align: center;
    font-family: 'Dancing Script', cursive;
    font-weight: 500;
    font-size: 110px;
    line-height: 1.2;
    color: var(--deep-green);
    margin: 0;
  }
  .product-descriptor {
    position: absolute;
    top: 350px;
    left: 0;
    width: 100%;
    text-align: center;
    font-family: 'Dancing Script', cursive;
    font-weight: 500;
    font-size: 210px;
    line-height: 1;
    margin: 0;
  }
  .product-name {
    position: absolute;
    top: 610px;
    left: 0;
    width: 100%;
    text-align: center;
    font-weight: 300;
    font-size: 178px;
    letter-spacing: 4px;
    line-height: 1;
    margin: 0;
  }
  .slogan {
    position: absolute;
    top: 800px;
    left: 90px;
    margin: 0;
    padding: 0;
    list-style: none;
    font-weight: 300;
    font-size: 40px;
    letter-spacing: 4px;
  }
  .slogan li {
    padding: 4px 0 6px;
    border-bottom: 1.5px solid var(--rule-brown);
    width: max-content;
    margin-bottom: 6px;
  }
  .product-photo {
    position: absolute;
    left: 560px;
    top: 800px;
    width: 580px;
    height: 300px;
    border-radius: 140px 60px 120px 140px;
    background: radial-gradient(ellipse at 60% 50%, var(--nut-tan) 0%, var(--nut-green) 65%, rgba(127,154,60,0) 100%);
  }
  .certification-seal {
    position: absolute;
    left: 90px;
    top: 1010px;
    width: 120px;
    height: 120px;
    border-radius: 50%;
    background: var(--seal-fill);
  }
  .tagline {
    position: absolute;
    right: 60px;
    bottom: 40px;
    margin: 0;
    font-weight: 300;
    font-size: 44px;
    letter-spacing: 3px;
  }
</style>
</head>
<body>
  <main class="package-front">
    <h1 class="brand-name">Tiller's Pantry</h1>
    <p class="product-descriptor">organic</p>
    <h2 class="product-name">PISTACHIO</h2>
    <ul class="slogan">
      <li>A gift from the farm</li>
      <li>brought fresh to</li>
      <li>your door</li>
    </ul>
    <div class="product-photo" role="img" aria-label="Photo of shelled and in-shell pistachios with green leaves"></div>
    <div class="certification-seal" role="img" aria-label="Organic certification seal"></div>
    <p class="tagline">Indulge. Nourish. Enjoy</p>
  </main>
</body>
</html>
```